Luxury Business Card Design for High-End Window Treatments

Gilded Slatworks
Custom Plantation Shutters & Architectural Shading Systems

⸻

BACK

Daniel Trevick
Owner

Custom Interior & Exterior Window Treatments

919-555-0148
gildedslatworks.com

I have included a picture that I’m hoping we can use on the back, but I’m also wondering if you can get rid of the ladder? Should we get rid of shutters , shades and blinds underneath Gilded Slatworks?

Target Market(s)

High-end residential homeowners, custom home builders, architects, interior designers, and luxury renovation clients seeking premium plantation shutters and motorized architectural shading systems.

Industry/Entity Type

Custom Window treatments

Contact Information for Business Card

Front Gilded Slatworks Custom Plantation Shutters Motorized Architectural Shading Systems BACK Daniel Trevick Owner 919-555-0148 GildedSlatworks.com Custom Interior & Exterior Window Treatments By Appointment

Requirements
Nice to have
• Not 100% sure on nice to halves or the color but you can definitely check out my website to get a better understanding of what I’m trying to do

```html
<!DOCTYPE html>
<html lang="en">
<head>
<meta charset="utf-8">
<title>Gilded Slatworks – Business Card</title>
<link rel="stylesheet" href="https://fonts.googleapis.com/css2?family=Libre+Baskerville:wght@400;700&family=Lora:wght@400&family=Lato:wght@400&display=swap">
<style>
  :root {
    --backdrop: #2b2929;
    --card: #0d0d0e;
    --card-edge: #141415;
    --gold: #d9b44a;
    --gold-soft: #c9a640;
  }
  * { box-sizing: border-box; margin: 0; padding: 0; }
  html, body {
    width: 1200px;
    height: 939px;
    overflow: hidden;
    background: var(--backdrop);
  }
  .canvas {
    position: relative;
    width: 1200px;
    height: 939px;
  }
  .card {
    position: absolute;
    width: 560px;
    height: 320px;
    border-radius: 22px;
    background: linear-gradient(160deg, var(--card-edge), var(--card) 60%);
    border: 1.5px solid var(--gold);
    box-shadow: 0 14px 30px rgba(0,0,0,0.45);
    color: var(--gold);
    text-align: center;
  }
  .card--front { left: 90px; top: 100px; }
  .card--back { left: 550px; top: 510px; }

  .brand-name {
    position: absolute;
    left: 0; right: 0;
    top: 78px;
    font-family: "Lora", serif;
    font-weight: 400;
    font-size: 46px;
    line-height: 1.1;
    letter-spacing: 0.5px;
  }
  .product-lines {
    position: absolute;
    left: 0; right: 0;
    top: 150px;
    font-family: "Lora", serif;
    font-size: 20px;
    word-spacing: 18px;
    color: var(--gold-soft);
  }
  .tagline {
    position: absolute;
    left: 0; right: 0;
    bottom: 32px;
    font-family: "Libre Baskerville", serif;
    font-size: 10.5px;
    letter-spacing: 0.3px;
    text-transform: uppercase;
  }

  .person-name {
    position: absolute;
    left: 0; right: 0;
    top: 92px;
    font-family: "Libre Baskerville", serif;
    font-weight: 700;
    font-size: 21px;
    letter-spacing: 0.5px;
    text-transform: uppercase;
  }
  .role {
    position: absolute;
    left: 50%;
    top: 126px;
    transform: translateX(-50%);
    display: flex;
    align-items: center;
    gap: 6px;
    font-family: "Lato", sans-serif;
    font-size: 13px;
  }
  .role::before, .role::after {
    content: "";
    width: 56px;
    height: 1px;
    background: var(--gold);
  }
  .contact {
    position: absolute;
    left: 0; right: 0;
    top: 152px;
    font-family: "Lato", sans-serif;
    font-size: 14px;
    line-height: 1.35;
  }
</style>
</head>
<body>
<main class="canvas">
  <section class="card card--front" aria-label="Card front">
    <h1 class="brand-name">Gilded Slatworks</h1>
    <p class="product-lines">Shutters Shades Blinds</p>
    <p class="tagline">Custom Plantation Shutters &amp; Motorized Architectural Shading Systems</p>
  </section>

  <section class="card card--back" aria-label="Card back">
    <h2 class="person-name">Daniel Trevick</h2>
    <p class="role">Owner</p>
    <p class="contact">919-555-0148<br>gildedslatworks.com</p>
    <p class="tagline">Custom Interior &amp; Exterior Window Treatments</p>
  </section>
</main>
</body>
</html>
```